Web Design

Looking for web designer for total service. We would like to make it in English and Japanese for now. Also need to make Tablet version. Our website is www.corvelpicks.com and www.brindaleads .com

```html
<!DOCTYPE html>
<html lang="en">
<head>
<meta charset="utf-8">
<title>Corvel Picks</title>
<link href="https://fonts.googleapis.com/css2?family=Abel&family=Open+Sans:wght@400;600&display=swap" rel="stylesheet">
<style>
:root{
  --cream:#f3eee2;
  --panel:#ebe6d8;
  --panel-line:#8c8a80;
  --orange:#e8652f;
  --blue:#1f4e86;
  --link-blue:#2a5a8c;
  --text:#333;
  --muted:#555;
  --grey-band:#ededed;
  --footer:#2b2b2b;
  --footer-text:#b9b9b9;
}
*{margin:0;padding:0;box-sizing:border-box}
html,body{width:781px;height:1200px;overflow:hidden;background:#fff}
body{position:relative;font-family:"Open Sans",Arial,sans-serif;color:var(--text)}
.abs{position:absolute}
.heading{font-family:"Abel","Arial Narrow",sans-serif;font-weight:400}

.site-header{left:0;top:0;width:781px;height:52px;background:var(--cream)}
.brand{left:86px;top:17px;font-family:"Abel",sans-serif;font-size:15px;color:var(--blue);letter-spacing:1px;line-height:18px}
.main-nav a{position:absolute;top:20px;font-size:8.5px;color:#444;text-decoration:none;white-space:nowrap}
.main-nav a.active{color:var(--orange)}
.cart{left:623px;top:13px;width:26px;height:26px;border-radius:50%;background:var(--blue)}
.flag{top:21px;width:12px;height:8px}

.hero{left:0;top:52px;width:781px;height:271px;background:radial-gradient(ellipse at 62% 40%,#d8c7a4 0%,#a99576 18%,#4a4640 42%,#2e2c2a 70%,#3a3835 100%)}
.hero-title{left:86px;top:174px;font-size:22px;line-height:26px;color:#fff;letter-spacing:.3px}
.hero-text{left:86px;top:226px;width:165px;font-size:7.5px;line-height:12.5px;color:#fff}
.hero-arrow{top:175px;width:25px;height:25px}

.feature{top:344px;width:193px;height:145px;background:var(--panel);padding:5px}
.feature-inner{width:100%;height:100%;border:1px solid var(--panel-line);text-align:center}
.feature-icon{margin:17px auto 0;width:44px;height:42px;border-radius:6px;background:linear-gradient(#d5e4f1,#c2d7ea)}
.feature-title{margin-top:6px;font-size:17px;color:var(--orange);letter-spacing:.3px}
.feature-text{margin:6px auto 0;width:175px;font-size:7px;line-height:11.5px;color:#333}

.divider{top:542px;height:1px;background:#c9c9c9}
.divider-dot{left:374px;top:526px;width:32px;height:32px;border-radius:50%;background:var(--panel)}

.section-title{width:781px;text-align:center;font-size:17px;color:var(--orange);letter-spacing:.3px}
.product-photo{top:638px;width:141px;height:140px;background:linear-gradient(180deg,#ecebe8 0%,#dcd9d3 100%)}
.product-bag{position:absolute;left:42px;top:12px;width:57px;height:120px;border-radius:3px}
.product-name{top:784px;width:141px;text-align:center;font-size:9px;color:var(--link-blue)}
.chevron{top:700px;width:12px;height:16px}

.news-band{left:0;top:846px;width:781px;height:192px;background:var(--grey-band)}
.news-lead{left:0;top:918px;width:781px;text-align:center;font-size:10px;color:#222}
.news-text{left:86px;top:934px;width:609px;text-align:center;font-size:7px;line-height:12px;color:#555}
.read-more{left:367px;top:965px;width:47px;height:21px;border:1px solid #777;background:#fff;font-size:7px;color:#444;text-align:center;line-height:19px}

.site-footer{left:0;top:1038px;width:781px;height:162px;background:var(--footer)}
.footer-title{top:1055px;font-size:15px;color:#fff;letter-spacing:.3px}
.footer-line{top:1081px;font-size:7px;line-height:15.6px;color:var(--footer-text)}
.social{top:1083px;width:10px;height:10px;border-radius:50%;background:#8d8d8d}
.footer-rule{left:86px;top:1158px;width:609px;height:1px;background:#6a6a6a}
.copyright{left:0;top:1173px;width:781px;text-align:center;font-size:7px;color:var(--footer-text)}
</style>
</head>
<body>

<header class="abs site-header">
  <div class="abs brand">CORVEL PICKS</div>
  <nav class="main-nav">
    <a class="active" style="left:214px">Home</a>
    <a style="left:256px">About Us</a>
    <a style="left:310px">Our Products</a>
    <a style="left:379px">Shop</a>
    <a style="left:417px">Suppliers</a>
    <a style="left:472px">Inquiries</a>
    <a style="left:524px">Careers</a>
    <a style="left:572px">Contact Us</a>
  </nav>
  <svg class="abs cart" viewBox="0 0 26 26" aria-label="Cart">
    <circle cx="13" cy="13" r="13" fill="#1f4e86"/>
    <path d="M8 9h2l1.5 6h5.5l1.2-4.5H10.6" fill="none" stroke="#fff" stroke-width="1.3" stroke-linejoin="round"/>
    <circle cx="12" cy="17" r="1" fill="#fff"/><circle cx="16.5" cy="17" r="1" fill="#fff"/>
  </svg>
  <svg class="abs flag" style="left:663px" viewBox="0 0 12 8" aria-label="Japanese">
    <rect width="12" height="8" fill="#fff" stroke="#ccc" stroke-width=".5"/><circle cx="6" cy="4" r="2.2" fill="#c8102e"/>
  </svg>
  <svg class="abs flag" style="left:681px" viewBox="0 0 12 8" aria-label="English">
    <rect width="12" height="8" fill="#23407a"/>
    <path d="M0 0L12 8M12 0L0 8" stroke="#fff" stroke-width="1.4"/>
    <path d="M6 0V8M0 4H12" stroke="#fff" stroke-width="2.2"/>
    <path d="M6 0V8M0 4H12" stroke="#c8102e" stroke-width="1.1"/>
  </svg>
</header>

<section class="abs hero" role="img" aria-label="Grilled rice triangles on a dark plate"></section>
<svg class="abs hero-arrow" style="left:29px" viewBox="0 0 25 25" aria-label="Previous slide">
  <circle cx="12.5" cy="12.5" r="11.5" fill="#fff" stroke="#1f4e86" stroke-width="2"/>
  <path d="M14.5 7.5L9.5 12.5L14.5 17.5" fill="none" stroke="#1f4e86" stroke-width="2.2"/>
</svg>
<svg class="abs hero-arrow" style="left:726px" viewBox="0 0 25 25" aria-label="Next slide">
  <circle cx="12.5" cy="12.5" r="11.5" fill="#fff" stroke="#1f4e86" stroke-width="2"/>
  <path d="M10.5 7.5L15.5 12.5L10.5 17.5" fill="none" stroke="#1f4e86" stroke-width="2.2"/>
</svg>
<h1 class="abs heading hero-title">RELY ON BUSINEES<br>EXPERTIN HAWAII.</h1>
<p class="abs hero-text">We also do marketing consulting for customers who want to sell their products in Hawaii or the mainland USA.</p>

<div class="abs feature" style="left:86px"><div class="feature-inner">
  <div class="feature-icon" role="img" aria-label="Milk bottle icon"></div>
  <h2 class="heading feature-title">WHAT WE DO</h2>
  <p class="feature-text">Maecenas vel tortor accumsan quam varius imper diet vel eget elit. Aenean facilisis tincidunt lectus, id dictum nisi luctus eget.</p>
</div></div>
<div class="abs feature" style="left:294px"><div class="feature-inner">
  <div class="feature-icon" role="img" aria-label="Chef hat icon"></div>
  <h2 class="heading feature-title">ABOUT US</h2>
  <p class="feature-text">Maecenas vel tortor accumsan quam varius imper diet vel eget elit. Aenean facilisis tincidunt lectus, id dictum nisi luctus eget.</p>
</div></div>
<div class="abs feature" style="left:501px"><div class="feature-inner">
  <div class="feature-icon" role="img" aria-label="Team icon"></div>
  <h2 class="heading feature-title">CAREERS</h2>
  <p class="feature-text">Maecenas vel tortor accumsan quam varius imper diet vel eget elit. Aenean facilisis tincidunt lectus, id dictum nisi luctus eget.</p>
</div></div>

<div class="abs divider" style="left:86px;width:283px"></div>
<div class="abs divider" style="left:411px;width:284px"></div>
<div class="abs divider-dot"></div>

<h2 class="abs heading section-title" style="left:0;top:606px">OUR PRODUCTS</h2>
<svg class="abs chevron" style="left:36px" viewBox="0 0 12 16" aria-label="Previous"><path d="M9 2L3 8L9 14" fill="none" stroke="#777" stroke-width="2.2"/></svg>
<svg class="abs chevron" style="left:733px" viewBox="0 0 12 16" aria-label="Next"><path d="M3 2L9 8L3 14" fill="none" stroke="#777" stroke-width="2.2"/></svg>

<div class="abs product-photo" style="left:86px" role="img" aria-label="Buttermilk pancake mix bag"><div class="product-bag" style="background:linear-gradient(#c9a97a,#a9c3d8 40%,#b7cde0)"></div></div>
<div class="abs product-photo" style="left:242px" role="img" aria-label="Macadamia nut pancake mix bag"><div class="product-bag" style="background:linear-gradient(#c9a97a,#e7a24a 40%,#e8a956)"></div></div>
<div class="abs product-photo" style="left:398px" role="img" aria-label="Acai pancake mix bag"><div class="product-bag" style="background:linear-gradient(#c9a97a,#ee8fae 40%,#f0a3bd)"></div></div>
<div class="abs product-photo" style="left:553px" role="img" aria-label="Banana pancake mix bag"><div class="product-bag" style="background:linear-gradient(#c9a97a,#e7df6a 40%,#ece57a)"></div></div>
<p class="abs product-name" style="left:86px">Buttermilk taste</p>
<p class="abs product-name" style="left:242px">Macadamia nut taste</p>
<p class="abs product-name" style="left:398px">Asai taste</p>
<p class="abs product-name" style="left:553px">Banana taste</p>

<section class="abs news-band"></section>
<h2 class="abs heading section-title" style="left:0;top:893px">WHAT'S NEW</h2>
<p class="abs news-lead">Quisque aliquet ex nec est vestibulum pulvinar convallis molestie enim sit amet efficitur</p>
<p class="abs news-text">Vivamus eleifend vitae nulla vel malesuada. In ac malesuada lacus, et consectetur ante. Fusce vitae lectus sit amet mi pulvinar maximus. Aenean placerat, nibh vel accumsan aliquet, magna nibh accumsan nibh, ac tempus nunc ipsum ac tellus.</p>
<div class="abs read-more">Read More</div>

<footer class="abs site-footer"></footer>
<h3 class="abs heading footer-title" style="left:86px">LINKS</h3>
<p class="abs footer-line" style="left:86px">Home<br>About Us<br>Our Products<br>Shop</p>
<p class="abs footer-line" style="left:143px">Suppliers<br>Inquiries<br>Careers<br>Contact Us</p>
<h3 class="abs heading footer-title" style="left:248px">CONTACT INFO</h3>
<p class="abs footer-line" style="left:249px">415 Maple Crest Avenue 12, Lindport HI 96000<br>Tel: (555) 014 - 2290<br>Fax: (555) 014-7781<br>Email:info@brindaleads.com</p>
<h3 class="abs heading footer-title" style="left:449px">WORKING HOURS</h3>
<p class="abs footer-line" style="left:450px">Mon - Fri: 8: 00 am - 4: 45 pm</p>
<h3 class="abs heading footer-title" style="left:605px">FOLLOW US ON</h3>
<div class="abs social" style="left:604px"></div>
<div class="abs social" style="left:623px"></div>
<div class="abs footer-rule"></div>
<p class="abs copyright">Copyright © 2018 Corvel Picks. All rights reserved.</p>

</body>
</html>
```